Tolvik Commercial Cleaning is lookong for a new business card design.

A fresh new design that's professional and stylish. We need a serious upgrade to our business cards. I have included pictures of our existing ones. Our clients include professional individuals and business owners. We woupdblike something professional and upbeat. Please have fun and see what you come uo with.

Target Market(s)

Property managers, business owners, facility managers and other similar professionals

Industry/Entity Type

Janitorial

Contact Information for Business Card

Name, cell, office number, email, web address

Font styles to use
Sans Serif

Colors

Designer to choose colors to be used in the design.

Requirements
Must have
• please use the green color in our logo
Nice to have
• Bar code
Should not have
• Address

```html
<!DOCTYPE html>
<html lang="en">
<head>
<meta charset="utf-8">
<title>Tolvik Commercial Cleaning – Business Card</title>
<link rel="stylesheet" href="https://fonts.googleapis.com/css2?family=Open+Sans:wght@400;600;700&display=swap">
<style>
  :root {
    --stage: #e9e9ec;
    --card-dark: #202024;
    --brand-green: #3ab75a;
    --brand-blue: #3f74ad;
    --deep-blue: #0d5896;
    --ink-light: #f2f2f2;
    --decor-dark: #141416;
  }
  * { box-sizing: border-box; margin: 0; padding: 0; }
  html, body { width: 1200px; height: 780px; overflow: hidden; }
  body {
    background: var(--stage);
    font-family: "Open Sans", Arial, sans-serif;
    display: flex;
    align-items: center;
    justify-content: center;
    gap: 48px;
  }
  .card {
    position: relative;
    width: 540px;
    height: 309px;
    border-radius: 18px;
    overflow: hidden;
    background: var(--card-dark);
    box-shadow: 0 6px 18px rgba(0,0,0,0.18);
  }

  /* Front */
  .front .brand-name {
    position: absolute;
    left: 34px;
    top: 30px;
    width: 240px;
    font-weight: 700;
    font-size: 30px;
    line-height: 1.05;
    color: var(--brand-green);
  }
  .front .decor-name {
    position: absolute;
    right: -6px;
    bottom: -22px;
    font-weight: 700;
    font-size: 120px;
    line-height: 1;
    color: var(--decor-dark);
    letter-spacing: -2px;
  }
  .front .contact {
    position: absolute;
    left: 34px;
    top: 170px;
    list-style: none;
    color: var(--ink-light);
    font-size: 14px;
    line-height: 1.55;
  }
  .front .contact li { display: flex; align-items: center; gap: 8px; }
  .front .contact svg { width: 12px; height: 12px; fill: var(--brand-green); flex: none; }
  .front .person {
    position: absolute;
    right: 40px;
    top: 104px;
    font-weight: 600;
    font-size: 27px;
    letter-spacing: 0.5px;
  }
  .person .first { color: var(--brand-green); }
  .person .last { color: var(--brand-blue); }
  .front .edge-tab {
    position: absolute;
    right: 0;
    top: 104px;
    width: 22px;
    height: 38px;
    background: var(--brand-green);
  }

  /* Back */
  .back .blue-band {
    position: absolute;
    left: 0;
    right: 0;
    top: 28px;
    bottom: 44px;
    background: var(--brand-blue);
    display: flex;
    align-items: center;
    justify-content: center;
  }
  .back .brand-name {
    font-weight: 700;
    font-size: 40px;
    line-height: 1.1;
    color: var(--deep-blue);
    text-align: center;
  }
</style>
</head>
<body>
  <section class="card front" aria-label="Business card front">
    <div class="decor-name" aria-hidden="true">Tolvik</div>
    <div class="brand-name">Tolvik Commercial Cleaning</div>
    <div class="person"><span class="first">Marco</span> <span class="last">Ellison</span></div>
    <div class="edge-tab"></div>
    <ul class="contact">
      <li>
        <svg viewBox="0 0 24 24" aria-hidden="true"><path d="M6.6 10.8a15.1 15.1 0 0 0 6.6 6.6l2.2-2.2c.3-.3.7-.4 1-.2 1.1.4 2.3.6 3.6.6.6 0 1 .4 1 1V20c0 .6-.4 1-1 1A17 17 0 0 1 3 4c0-.6.4-1 1-1h3.5c.6 0 1 .4 1 1 0 1.3.2 2.5.6 3.6.1.3 0 .7-.2 1z"/></svg>
        (555) 014-2290
      </li>
      <li>
        <svg viewBox="0 0 24 24" aria-hidden="true"><path d="M2 5h20v14H2zm2 2v.4l8 5 8-5V7zm0 2.7V17h16V9.7l-8 5z"/></svg>
        marco@tolvikcleaning.com
      </li>
      <li>
        <svg viewBox="0 0 24 24" aria-hidden="true"><path d="M12 2a10 10 0 1 0 0 20 10 10 0 0 0 0-20zm6.9 6h-3a15 15 0 0 0-1.3-3.9A8 8 0 0 1 18.9 8zM12 4c.8 1.2 1.5 2.5 1.9 4h-3.8c.4-1.5 1.1-2.8 1.9-4zM4.3 14a8 8 0 0 1 0-4h3.4a16 16 0 0 0 0 4zm.8 2h3a15 15 0 0 0 1.3 3.9A8 8 0 0 1 5.1 16zm3-8h-3a8 8 0 0 1 4.3-3.9A15 15 0 0 0 8.1 8zM12 20c-.8-1.2-1.5-2.5-1.9-4h3.8c-.4 1.5-1.1 2.8-1.9 4zm2.3-6H9.7a14 14 0 0 1 0-4h4.6a14 14 0 0 1 0 4zm.3 5.9a15 15 0 0 0 1.3-3.9h3a8 8 0 0 1-4.3 3.9zm1.7-5.9a16 16 0 0 0 0-4h3.4a8 8 0 0 1 0 4z"/></svg>
        www.tolvikcleaning.com
      </li>
    </ul>
  </section>

  <section class="card back" aria-label="Business card back">
    <div class="blue-band">
      <div class="brand-name">Tolvik Commercial Cleaning</div>
    </div>
  </section>
</body>
</html>
```